Business Cards for IT Consulting Company (Managed Service Provider)

I am looking to have some business cards printed and would like some designs. We are an IT Consulting company based in Vancouver BC. I would like a nice clean and modern look to the cards. I have uploaded all the versions of my logo so parts can be used as needed. Here is a snippit from our website homepage:

Quillbrook Networks Ltd. is an IT Solutions Partner located in Vancouver BC, Canada. We offer IT solutions and support to customers in the greater Vancouver Area. With expertise in Microsoft platforms, as well as Linux and Mac OSX and over 12 years experience in the IT industry, Quillbrook Networks is dedicated to offering our clients top quality service and products. We take pride in the solutions we offer our customers. The greatest compliment a client can give us is to recommend our services.

Quillbrook Networks Ltd. offers a wide range of IT services from onsite service to remote support and managed service solutions. This allows clients to choose the support path that best suits their company’s needs. Supporting many different sized companies from small to enterprise level over the past 12 years Quillbrook Networks has the experience and expertise needed to ensure things run smoothly. Allowing our clients to focus on doing business.

Revolutionizing the way IT services are delivered.

Quillbrook Networks is dedicated to providing our clients with IT solutions that work and grow with them for years to come. This philosophy helps save money in the long run instead of replacing equipment constantly. Far too often IT solutions are not well thought out and while possibly solving the problem at hand, require replacement due to growth or quality within a very short time frame. Quillbrook Networks takes pride in providing solutions that will last and be able to accommodate growth without the need for replacement.

Industry/Entity Type

Information Technology

Contact Information for Business Card

Quillbrook Networks Ltd.
(Employee Name)
Eml: (Employees Email Address)
Web: quillbrook.me
Ph: 604-555-0148

Font styles to use
Serif
Sans Serif

Requirements
Must have
• The Company logo and company colors.
Nice to have
• - Our tag line: "Revolutionizing IT Services" or "Revolutionizing the way IT services are delivered."
• - Also I really like the idea of nature and technology together blending which is sort of where my logo came from so integrating that somehow onto the business cards would be great.

```html
<!DOCTYPE html>
<html lang="en">
<head>
<meta charset="utf-8">
<title>Quillbrook Networks Ltd. — Business Card</title>
<link rel="stylesheet" href="https://fonts.googleapis.com/css2?family=Montserrat:wght@400;500;600;700&display=swap">
<style>
  :root {
    --page: #2a2a2b;
    --card-grey: #5e5f61;
    --ink-grey: #58595b;
    --brand-blue: #1ba9e6;
    --white: #ffffff;
  }
  * { box-sizing: border-box; margin: 0; padding: 0; }
  html, body { width: 1200px; height: 900px; overflow: hidden; }
  body {
    background: var(--page);
    font-family: "Montserrat", sans-serif;
    position: relative;
  }
  .card {
    position: absolute;
    width: 560px;
    height: 320px;
    border-radius: 22px;
    overflow: hidden;
  }

  /* Back of card */
  .card-back { left: 120px; top: 90px; background: var(--card-grey); }
  .back-brand {
    position: absolute; left: 0; right: 0; top: 100px;
    display: flex; align-items: center; justify-content: center; gap: 14px;
  }
  .brand-square { width: 22px; height: 22px; background: var(--brand-blue); }
  .back-brand .brand-name {
    color: var(--brand-blue); font-weight: 600; font-size: 40px; letter-spacing: 0.5px;
  }
  .tagline-band {
    position: absolute; left: 0; right: 0; top: 238px; height: 34px;
    background: var(--brand-blue);
    display: flex; align-items: center; justify-content: center;
  }
  .tagline {
    color: var(--white); font-weight: 500; font-size: 16px; letter-spacing: 1px;
  }

  /* Front of card */
  .card-front { left: 520px; top: 490px; background: var(--white); }
  .front-wave { position: absolute; inset: 0; }
  .front-brand {
    position: absolute; left: 44px; top: 58px;
    display: flex; align-items: center; gap: 14px;
  }
  .front-brand .brand-square { width: 26px; height: 26px; }
  .front-brand .brand-name {
    color: var(--brand-blue); font-weight: 600; font-size: 30px; line-height: 1.1;
  }
  .person { position: absolute; left: 44px; top: 248px; }
  .person-name {
    color: var(--white); font-weight: 700; font-size: 20px; letter-spacing: 1.5px;
  }
  .person-title {
    color: var(--ink-grey); font-weight: 600; font-size: 11px; letter-spacing: 2px;
    text-align: right; margin-top: 2px;
  }
  .divider {
    position: absolute; left: 300px; top: 222px; width: 1.5px; height: 70px;
    background: rgba(255,255,255,0.7);
  }
  .contact-list {
    position: absolute; left: 318px; top: 222px; list-style: none;
    color: var(--white); font-weight: 600; font-size: 13px;
  }
  .contact-list li { display: flex; align-items: center; gap: 8px; height: 23px; }
  .contact-list svg { width: 12px; height: 12px; flex: none; }
</style>
</head>
<body>

  <section class="card card-back">
    <div class="back-brand">
      <span class="brand-square"></span>
      <span class="brand-name">Quillbrook</span>
    </div>
    <div class="tagline-band">
      <p class="tagline">Revolutionizing IT Services</p>
    </div>
  </section>

  <section class="card card-front">
    <svg class="front-wave" viewBox="0 0 560 320" width="560" height="320" aria-hidden="true">
      <path d="M0 232 Q 340 232 560 62 L560 320 L0 320 Z" fill="var(--brand-blue)"/>
      <path d="M0 226 Q 340 226 560 54" fill="none" stroke="var(--ink-grey)" stroke-width="5"/>
    </svg>

    <div class="front-brand">
      <span class="brand-square"></span>
      <span class="brand-name">Quillbrook<br>Networks Ltd.</span>
    </div>

    <div class="person">
      <p class="person-name">MARLON ASHBY</p>
      <p class="person-title">DIRECTOR</p>
    </div>

    <div class="divider"></div>

    <ul class="contact-list">
      <li>
        <svg viewBox="0 0 12 12" aria-hidden="true"><path d="M2.5 1 L4.5 1 L5.3 3.6 L4 4.6 Q5 7 7.4 8 L8.4 6.7 L11 7.5 L11 9.5 Q11 11 9.5 11 Q1 10 1 2.5 Q1 1 2.5 1 Z" fill="var(--ink-grey)"/></svg>
        604-555-0148
      </li>
      <li>
        <svg viewBox="0 0 12 12" aria-hidden="true"><rect x="0.8" y="2.3" width="10.4" height="7.4" fill="none" stroke="var(--ink-grey)" stroke-width="1.3"/><path d="M1 2.6 L6 6.4 L11 2.6" fill="none" stroke="var(--ink-grey)" stroke-width="1.3"/></svg>
        info@marlonashby.com
      </li>
      <li>
        <svg viewBox="0 0 12 12" aria-hidden="true"><circle cx="6" cy="6" r="5.2" fill="var(--ink-grey)"/><path d="M0.8 6 H11.2 M6 0.8 Q3 6 6 11.2 M6 0.8 Q9 6 6 11.2" fill="none" stroke="var(--brand-blue)" stroke-width="0.9"/></svg>
        www.quillbrook.me
      </li>
    </ul>
  </section>

</body>
</html>
```